Business Cards for a law firm

Business cards for our law firm. Use our silhoette logo and OAK PARTNERS - check our website (www.oakpartners.example)

Contact Information for Business Card

our silhouette logo, OAK PARTNERS, 800-555-0147, Dorian Pemberton, dorian@oakpartners.example

Requirements
Must have
• our silhouette logo, OAK PARTNERS, 800-555-0147, Dorian Pemberton, dorian@oakpartners.example

```html
<!DOCTYPE html>
<html lang="en">
<head>
<meta charset="utf-8">
<title>Oak Partners – Business Cards</title>
<link rel="stylesheet" href="https://fonts.googleapis.com/css2?family=Montserrat:wght@800&family=Roboto:wght@400&display=swap">
<style>
  :root {
    --page-bg: #16181d;
    --card-navy: #13265a;
    --card-navy-deep: #0e1d47;
    --figure-dark: #0b1638;
    --figure-light: #3a5aa8;
    --ink-white: #ffffff;
  }
  * { margin: 0; padding: 0; box-sizing: border-box; }
  html, body {
    width: 1200px; height: 963px; overflow: hidden;
    background: var(--page-bg);
  }
  .canvas {
    position: relative; width: 1200px; height: 963px;
  }
  .card {
    position: absolute; left: 250px;
    width: 700px; height: 400px;
    background: radial-gradient(ellipse at 45% 45%, #17306e 0%, var(--card-navy) 55%, var(--card-navy-deep) 100%);
    overflow: hidden;
    box-shadow: 0 10px 30px rgba(0,0,0,.5);
  }
  .card--front { top: 60px; }
  .card--back { top: 503px; }

  .figure-area {
    position: absolute; top: 0; width: 190px; height: 400px;
    background: linear-gradient(180deg, var(--figure-dark) 0%, var(--figure-dark) 45%, var(--figure-light) 100%);
    opacity: .85;
  }
  .card--front .figure-area { left: 60px; }
  .card--back .figure-area { right: 40px; top: 120px; height: 280px; }

  .wordmark {
    font-family: "Montserrat", sans-serif; font-weight: 800;
    color: var(--ink-white); letter-spacing: 2px; white-space: nowrap;
  }
  .brand-lockup {
    position: absolute; left: 280px; top: 176px;
    display: flex; align-items: center; gap: 14px;
  }
  .brand-lockup .mark-dot {
    width: 34px; height: 34px; border-radius: 50%; background: var(--ink-white);
    flex: none;
  }
  .brand-lockup .wordmark { font-size: 32px; }

  .back-title {
    position: absolute; left: 150px; top: 50px; font-size: 32px;
  }
  .holder {
    position: absolute; left: 110px; top: 165px;
  }
  .holder-name {
    font-family: "Montserrat", sans-serif; font-weight: 800;
    font-size: 22px; letter-spacing: 1.5px; color: var(--ink-white);
    text-transform: uppercase; margin-bottom: 14px;
  }
  .contact-list { list-style: none; }
  .contact-item {
    display: flex; align-items: center; gap: 10px;
    font-family: "Roboto", sans-serif; font-size: 19px;
    color: var(--ink-white); line-height: 30px;
  }
  .contact-icon { width: 18px; height: 18px; flex: none; }
</style>
</head>
<body>
<main class="canvas">
  <section class="card card--front" aria-label="Card front">
    <div class="figure-area" role="img" aria-label="Large faint silhouette of a standing man in a jacket"></div>
    <div class="brand-lockup">
      <span class="mark-dot" aria-hidden="true"></span>
      <span class="wordmark">OAK PARTNERS</span>
    </div>
  </section>

  <section class="card card--back" aria-label="Card back">
    <div class="figure-area" role="img" aria-label="Large faint silhouette of a standing man with hands in pockets"></div>
    <h1 class="wordmark back-title">OAK PARTNERS</h1>
    <div class="holder">
      <p class="holder-name">Dorian Pemberton</p>
      <ul class="contact-list">
        <li class="contact-item">
          <svg class="contact-icon" viewBox="0 0 24 24" aria-hidden="true"><path fill="#fff" d="M6.6 10.8a15.1 15.1 0 0 0 6.6 6.6l2.2-2.2c.3-.3.7-.4 1-.2 1.1.4 2.300.6 3.6.6.6 0 1 .4 1 1V20c0 .6-.4 1-1 1A17 17 0 0 1 3 4c0-.6.4-1 1-1h3.5c.6 0 1 .4 1 1 0 1.3.2 2.5.6 3.6.1.3 0 .7-.2 1z"/></svg>
          <span>800-555-0147</span>
        </li>
        <li class="contact-item">
          <svg class="contact-icon" viewBox="0 0 24 24" aria-hidden="true"><rect x="2" y="5" width="20" height="14" rx="1.5" fill="#fff"/><path d="M3 6l9 7 9-7" fill="none" stroke="#13265a" stroke-width="2"/></svg>
          <span>dorian@oakpartners.example</span>
        </li>
        <li class="contact-item">
          <svg class="contact-icon" viewBox="0 0 24 24" aria-hidden="true"><circle cx="12" cy="12" r="10" fill="#fff"/><path d="M2 12h20M12 2c3 3 3 17 0 20M12 2c-3 3-3 17 0 20" fill="none" stroke="#13265a" stroke-width="1.5"/></svg>
          <span>www.oakpartners.example</span>
        </li>
      </ul>
    </div>
  </section>
</main>
</body>
</html>
```